Packaging design for a reclosable bag for our product

We have a logo, and we need to put it on packaging for our product and while we want the look to be simple, we want it to follow good design principles and also contain spaces for other product descriptions.

There will be 5 sizes at launch so I'd like 5 variations, one for each size.

I've included a few mockups of the type of bag that I made but they are all just rough ideas that I had.

I want the brand to look scientific and methodical and even a bit quirky, as in "wow this is a serious product but also a bit unusual."

```html
<!DOCTYPE html>
<html lang="en">
<head>
<meta charset="utf-8">
<title>NV3 Bias Lighting – Pouch Range</title>
<link rel="stylesheet" href="https://fonts.googleapis.com/css2?family=Jost:wght@400;500;700;800&display=swap">
<style>
  :root {
    --bg: #ffffff;
    --pouch: #232323;
    --pouch-line: #161616;
    --white: #ffffff;
    --blue: #1e9be6;
    --red: #e61e25;
    --band: #1a1a1a;
  }
  html, body {
    margin: 0;
    padding: 0;
    width: 1200px;
    height: 1200px;
    overflow: hidden;
    background: var(--bg);
    font-family: "Jost", Arial, sans-serif;
  }
  .canvas {
    position: relative;
    width: 1200px;
    height: 1200px;
  }
  .pouch {
    position: absolute;
    background: var(--pouch);
    border-radius: 18px 18px 2px 2px;
    overflow: hidden;
    color: var(--white);
  }
  .pouch--xl { left: 194px; top: 242px; width: 492px; height: 730px; --accent: var(--blue); }
  .pouch--l  { left: 574px; top: 346px; width: 448px; height: 660px; --accent: var(--red); }

  .size-stripe {
    position: absolute;
    left: 0; top: 0; bottom: 0;
    background: var(--accent);
  }
  .pouch--xl .size-stripe { width: 78px; }
  .pouch--l .size-stripe { width: 70px; }

  .stripe-band {
    position: absolute;
    left: 0;
    height: 18px;
    background: var(--band);
  }
  .pouch--xl .stripe-band { top: 533px; width: 78px; }
  .pouch--l .stripe-band { top: 474px; width: 70px; }

  .zip-line {
    position: absolute;
    height: 3px;
    background: var(--pouch-line);
  }
  .pouch--xl .zip-line { left: 78px; right: 0; top: 86px; }
  .pouch--xl .zip-line--b { top: 104px; }
  .pouch--l .zip-line { left: 70px; right: 0; top: 78px; }
  .pouch--l .zip-line--b { top: 96px; }

  .length-label {
    position: absolute;
    writing-mode: vertical-rl;
    transform: rotate(180deg);
    font-size: 30px;
    font-weight: 400;
    line-height: 1;
    color: var(--band);
    white-space: nowrap;
  }
  .length-label b { font-weight: 800; font-size: 34px; }
  .pouch--xl .length-label { left: 22px; bottom: 42px; }
  .pouch--l .length-label { left: 18px; bottom: 34px; }

  .label {
    position: absolute;
  }
  .pouch--xl .label { left: 112px; top: 412px; }
  .pouch--l .label { left: 102px; top: 356px; }

  .brand-name {
    margin: 0;
    font-size: 62px;
    font-weight: 700;
    line-height: 1;
    letter-spacing: -1px;
  }
  .product-name {
    margin: 18px 0 0;
    font-size: 30px;
    font-weight: 400;
    line-height: 1;
    letter-spacing: 0.5px;
  }
  .product-sub {
    margin: 6px 0 0;
    font-size: 17px;
    font-weight: 400;
    letter-spacing: 0.5px;
  }
  .size-code {
    margin: 8px 0 0;
    font-size: 32px;
    font-weight: 800;
    line-height: 1;
    color: var(--accent);
  }
  .spec {
    margin: 12px 0 0;
    font-size: 19px;
    line-height: 1.25;
    letter-spacing: 0.4px;
  }
  .spec span { display: block; font-size: 17.5px; }
</style>
</head>
<body>
<div class="canvas">

  <section class="pouch pouch--xl" aria-label="Extra large pouch">
    <div class="size-stripe"></div>
    <div class="stripe-band"></div>
    <div class="zip-line"></div>
    <div class="zip-line zip-line--b"></div>
    <div class="length-label"><b>5</b> meters</div>
    <div class="label">
      <h1 class="brand-name">NV3</h1>
      <p class="product-name">Bias Lighting</p>
      <p class="product-sub">Extra large</p>
      <p class="size-code">XL</p>
      <p class="spec">Simulated D65 CRI 90+<span>6500K White Bias Lighting</span></p>
    </div>
  </section>

  <section class="pouch pouch--l" aria-label="Large pouch">
    <div class="size-stripe"></div>
    <div class="stripe-band"></div>
    <div class="zip-line"></div>
    <div class="zip-line zip-line--b"></div>
    <div class="length-label"><b>4</b> meters</div>
    <div class="label">
      <h2 class="brand-name">NV3</h2>
      <p class="product-name">Bias Lighting</p>
      <p class="product-sub">Extra large</p>
      <p class="size-code">L</p>
      <p class="spec">Simulated D65 CRI 90+<span>6500K White Bias Lighting</span></p>
    </div>
  </section>

</div>
</body>
</html>
```